We need a redesign of our current website: www.halvenridgegroup.com. Halvenridge Group is a fully integrated hospitality development, management, and investment firm. We strive for leadership in each of our segments by building quality assets, exacting high standards of customer service, and focusing on returns for our investors and partners.

It is our mission to provide our guests an exceptional lodging experience; our clients an unsurpassed level of management in their properties; and create positive returns for our investors and partners. We achieve our mission via a company culture of transparency, ownership of our actions, and accountability for our results.

Target Market(s)

hotel owners, hotel developers, hotel investors, bankers

Industry/Entity Type

Hospitality

Requirements
Must have
• Our logo has to be there along with the quote and the ability to convey the following quote off of our current website: "Halvenridge was founded on the principles of integrity, honesty, loyalty, and trust. These convictions embody our company at every level, and show in every action."

```html
<!DOCTYPE html>
<html lang="en">
<head>
<meta charset="utf-8">
<title>Halvenridge Group</title>
<link rel="stylesheet" href="https://fonts.googleapis.com/css2?family=Arimo:wght@400;700&display=swap">
<style>
:root{
  --orange:#e08a00;
  --btn-top:#f2b100;
  --btn-bottom:#d98e00;
  --text:#2a2a2a;
  --muted:#777;
  --rule:#c4c4c4;
  --bar:#c6c6c6;
  --white:#fff;
}
*{margin:0;padding:0;box-sizing:border-box}
html,body{width:1200px;height:1182px;overflow:hidden;background:var(--white)}
body{position:relative;font-family:"Arimo",Arial,sans-serif;color:var(--text)}
.brand{position:absolute;left:21px;top:48px;display:flex;align-items:center;gap:14px}
.brand-mark{width:56px;height:56px;border-radius:50%;background:var(--orange)}
.brand-name{font-size:36px;font-weight:400;color:var(--orange);letter-spacing:1px}
.main-nav{position:absolute;top:65px;left:588px;display:flex;height:33px;align-items:center}
.main-nav a{font-size:17px;letter-spacing:.8px;color:#111;text-decoration:none;padding:0 22px;line-height:26px;border-right:1px solid var(--rule)}
.main-nav a.active{background:linear-gradient(var(--btn-top),var(--btn-bottom));color:var(--white);height:33px;line-height:33px;border-right:none;padding:0 22px;margin-right:3px}
.main-nav a:last-child{padding-right:14px}
.feature{position:absolute;top:146px;width:383px;height:542px}
.feature-photo{position:absolute;inset:0}
.feature-caption{position:absolute;left:0;right:0;top:473px;height:37px;background:rgba(20,20,20,.55);color:var(--white);font-weight:700;font-size:21px;letter-spacing:.6px;line-height:37px;padding:0 18px;text-align:right}
.f1{left:19px}.f1 .feature-photo{background:linear-gradient(135deg,#7a4a3a,#c8a08a 45%,#3a2a2a)}
.f2{left:410px;width:382px}.f2 .feature-photo{background:linear-gradient(135deg,#e8ecef,#9aa0a6 55%,#3a3d42)}
.f3{left:799px}.f3 .feature-photo{background:linear-gradient(135deg,#c9ccd0,#eceef0 45%,#8f949a)}
.teaser{position:absolute;top:715px;width:366px;font-size:16.5px;line-height:23.7px;text-align:justify;letter-spacing:.3px}
.teaser b{font-weight:700}
.t1{left:28px}.t2{left:417px}.t3{left:806px}
.btn{position:absolute;top:822px;width:95px;height:28px;background:linear-gradient(var(--btn-top),var(--btn-bottom));color:#111;font-size:13px;line-height:28px;padding-left:10px;text-decoration:none}
.btn svg{position:absolute;right:8px;top:10px}
.b1{left:28px}.b2{left:418px}.b3{left:806px}
.rule{position:absolute;left:19px;width:1162px;height:1px;background:var(--rule)}
.about-title{position:absolute;left:32px;top:893px;font-size:31px;font-weight:400;color:var(--orange)}
.about{position:absolute;left:28px;top:934px;width:1143px;font-size:16.5px;line-height:23.7px;text-align:justify;letter-spacing:.35px}
.about p+p{margin-top:23.7px}
.more{position:absolute;right:33px;top:1076px;font-size:13px;color:var(--muted);text-decoration:none;letter-spacing:.4px}
.foot-nav{position:absolute;left:19px;top:1127px;font-size:12px;letter-spacing:.8px;color:#555}
.foot-nav a{color:#555;text-decoration:none}
.foot-nav span{margin:0 6px}
.founding-quote{position:absolute;right:19px;top:1117px;width:720px;font-size:12px;line-height:16px;color:#555;text-align:right;letter-spacing:.2px}
.legal{position:absolute;left:19px;top:1157px;width:1162px;height:25px;background:var(--bar);text-align:center;font-size:13px;line-height:25px;color:#333;letter-spacing:.3px}
</style>
</head>
<body>
<header>
  <div class="brand"><div class="brand-mark"></div><div class="brand-name">Halvenridge Group</div></div>
  <nav class="main-nav">
    <a class="active" href="#">HOME</a><a href="#">SERVICES</a><a href="#">PROJECTS</a><a href="#">TEAM</a><a href="#">CONTACT</a>
  </nav>
</header>

<section>
  <div class="feature f1"><div class="feature-photo" role="img" aria-label="Smiling hotel front desk staff in uniform"></div><div class="feature-caption">HOSPITALITY DEVELOPMENT</div></div>
  <div class="feature f2"><div class="feature-photo" role="img" aria-label="Business team meeting around a conference table"></div><div class="feature-caption">MANAGEMENT</div></div>
  <div class="feature f3"><div class="feature-photo" role="img" aria-label="Hands reviewing financial charts with a pen"></div><div class="feature-caption">INVESTMENT FIRM</div></div>

  <p class="teaser t1"><b>When evaluating sites</b> for purchase and hotel development, our experienced team conducts the full array of feasibility studies and market analyses.</p>
  <p class="teaser t2"><b>Using proven strategies</b> we maximize poten&shy;tial and produce profitable results for your hotel, just as we do with our own.</p>
  <p class="teaser t3"><b>Halvenridge recognizes</b> that we are entrusted with investors' capital. In honoring this trust we aim to create and realize shareholder value through the acquisition,</p>

  <a class="btn b1" href="#">Read more<svg width="6" height="9" viewBox="0 0 6 9"><path d="M1 1l3.5 3.5L1 8" stroke="#111" fill="none" stroke-width="1.4"/></svg></a>
  <a class="btn b2" href="#">Read more<svg width="6" height="9" viewBox="0 0 6 9"><path d="M1 1l3.5 3.5L1 8" stroke="#111" fill="none" stroke-width="1.4"/></svg></a>
  <a class="btn b3" href="#">Read more<svg width="6" height="9" viewBox="0 0 6 9"><path d="M1 1l3.5 3.5L1 8" stroke="#111" fill="none" stroke-width="1.4"/></svg></a>
</section>

<div class="rule" style="top:879px"></div>

<section>
  <h2 class="about-title">About Halvenridge Group</h2>
  <div class="about">
    <p>Halvenridge Group is a fully integrated hospitality development, management, and investment firm. We strive for leadership in each of our segments by building quality assets, exacting high standards of customer service, and focusing on returns for our investors and partners.</p>
    <p>It is our mission to provide our guests an exceptional lodging experience; our clients an unsurpassed level of management in their properties; and create positive returns for our investors and partners. We achieve our mission via a company culture of transparency, ownership of our actions, and accountability for our results.</p>
  </div>
  <a class="more" href="#">Read more</a>
</section>

<div class="rule" style="top:1108px"></div>

<footer>
  <nav class="foot-nav"><a href="#">HOME</a><span>|</span><a href="#">SERVICES</a><span>|</span><a href="#">PROJECTS</a><span>|</span><a href="#">TEAM</a><span>|</span><a href="#">CONTACT</a></nav>
  <blockquote class="founding-quote">"Halvenridge was founded on the principles of integrity, honesty, loyalty, and trust. These convictions embody our company at every level, and show in every action."</blockquote>
  <div class="legal">© 2012 Halvenridge Group - Terms of Service - Privacy Policy - Program Policies</div>
</footer>
</body>
</html>
```